Natural Light/Organic/Documentary Photography Business

I like a simple, approachable, feminine, earthy/organic feel. Earth/neutral tones, nothing too loud or obnoxious. I like the watercolor look. I don't want anything too trendy or something I'll get tired of after a couple months. As far as colors, I am much more a fan of cream/taupe/blue/green...not a fan of pink or purple at all.

Target Market(s)

Weddings & Families

Industry/Entity Type

Wedding Photography

Contact Information for Business Card

website, email, phone number

Font styles to use
Other font styles liked:
• Horizontes, Gotham

Colors

Designer to choose colors to be used in the design.

Requirements
Must have
• Website: www.mirelhatchway.com
• Phone: 418.629.5073
• Email: mirel@mirelhatchway.com
Nice to have
• I like the watercolor look but its not necessary. I like simple/earthy tones. Nothing too loud or distracting. Simple & feminine without being too girly. I like an approachable/soft feel.
• Instagram: www.instagram.com/mirelhatchwayphotography/
Should not have
• NO loud colors or design or pattern. I do not want a photo of a camera or lens or anything cheesy like that.

```html
<!DOCTYPE html>
<html lang="en">
<head>
<meta charset="utf-8">
<title>Mirel Hatchway Photography – Business Card</title>
<link rel="stylesheet" href="https://fonts.googleapis.com/css2?family=Open+Sans:wght@400;600&display=swap">
<style>
  :root {
    --backdrop: #ece7e1;
    --card: #ffffff;
    --taupe: #887a70;
    --ink: #3f3f3f;
    --rule: #dfe3e8;
    --accent: #2f5f8f;
  }
  html, body {
    margin: 0;
    padding: 0;
    width: 1200px;
    height: 900px;
    overflow: hidden;
    background: var(--backdrop);
    font-family: "Open Sans", Arial, sans-serif;
  }
  .canvas {
    position: relative;
    width: 1200px;
    height: 900px;
  }
  .card {
    position: absolute;
    left: 330px;
    width: 556px;
    height: 344px;
    background: var(--card);
    box-shadow: 2px 3px 6px rgba(0, 0, 0, 0.18);
  }
  .card--front { top: 90px; }
  .card--back { top: 469px; }
  .card__frame {
    position: absolute;
    left: 33px;
    top: 36px;
    width: 482px;
    height: 268px;
    border: 4px solid var(--taupe);
  }
  .brand-name {
    position: absolute;
    left: 0;
    right: 0;
    top: 66px;
    margin: 0;
    text-align: center;
    font-size: 30px;
    font-weight: 400;
    letter-spacing: 1px;
    color: var(--taupe);
  }
  .contact {
    position: absolute;
    left: 0;
    right: 0;
    top: 180px;
    margin: 0;
    padding: 0;
    list-style: none;
    text-align: center;
    font-size: 16.5px;
    line-height: 20.5px;
    color: var(--ink);
  }
  .contact__label { font-weight: 600; }
  .contact__label--phone { color: var(--taupe); }
  .social {
    position: absolute;
    left: 42px;
    right: 42px;
    top: 207px;
  }
  .social__rule {
    position: relative;
    height: 1px;
    background: var(--rule);
  }
  .social__dot {
    position: absolute;
    left: 50%;
    top: -11px;
    width: 22px;
    height: 22px;
    margin-left: -11px;
    border-radius: 50%;
    background: var(--accent);
  }
  .social__link {
    margin: 20px 0 0;
    text-align: center;
    font-size: 17px;
    color: var(--ink);
  }
</style>
</head>
<body>
<main class="canvas">
  <section class="card card--front" aria-label="Business card front">
    <div class="card__frame">
      <h1 class="brand-name">Mirel Hatchway Photography</h1>
      <ul class="contact">
        <li><span class="contact__label contact__label--phone">P:</span> 418.629.5073</li>
        <li><span class="contact__label">E:</span> mirel@mirelhatchway.com</li>
        <li><span class="contact__label">W:</span> www.mirelhatchway.com</li>
      </ul>
    </div>
  </section>

  <section class="card card--back" aria-label="Business card back">
    <div class="card__frame">
      <h2 class="brand-name">Mirel Hatchway Photography</h2>
      <div class="social">
        <div class="social__rule"><span class="social__dot"></span></div>
        <p class="social__link">www.lumigram.com/mirelhatchwayphotography/</p>
      </div>
    </div>
  </section>
</main>
</body>
</html>
```